Tech business card design

We need an amazing business card design for our new business 'Pexla' a marketing tech startup based in Sydney, Australia. We provide an online marketplace for businesses to search and buy advertising media, connect with service providers and learn more about marketing. We wish to communicate 'cool tech', reliability and professionalism and design based around our logo.

Target Market(s)

Business Owners

Contact Information for Business Card

Name
Position
Email Address
Website
Phone Number

Font styles to use
Other font styles liked:
• Avenir & Avenir Next

Colors

Designer to choose colors to be used in the design.

```html
<!DOCTYPE html>
<html lang="en">
<head>
<meta charset="utf-8">
<title>Pexla Business Card</title>
<link href="https://fonts.googleapis.com/css2?family=Nunito+Sans:wght@400;700;800&display=swap" rel="stylesheet">
<style>
  :root {
    --stage: #a9a9ab;
    --paper: #ffffff;
    --navy: #1b1a45;
    --navy-card: #23224f;
    --white: #ffffff;
  }
  html, body {
    margin: 0;
    padding: 0;
    width: 1200px;
    height: 1200px;
    overflow: hidden;
    background: var(--stage);
    font-family: "Nunito Sans", sans-serif;
  }
  .card {
    position: absolute;
    left: 172px;
    width: 846px;
    height: 482px;
    border-radius: 26px;
    overflow: hidden;
  }
  .card-front { top: 94px; background: var(--paper); color: var(--navy); }
  .card-back { top: 612px; background: var(--navy-card); color: var(--white); }

  .wordmark {
    position: absolute;
    font-weight: 800;
    letter-spacing: -2px;
    line-height: 1;
    margin: 0;
  }
  .card-front .wordmark {
    left: 0; right: 0;
    top: 110px;
    text-align: center;
    font-size: 150px;
    color: var(--navy);
  }
  .identity {
    position: absolute;
    right: 512px;
    top: 280px;
    text-align: right;
    line-height: 1.05;
  }
  .identity .person { font-weight: 800; font-size: 32px; display: block; }
  .identity .role { font-weight: 400; font-size: 31px; display: block; }
  .divider {
    position: absolute;
    left: 362px;
    top: 272px;
    width: 2px;
    height: 80px;
    background: var(--navy);
  }
  .contacts {
    position: absolute;
    left: 395px;
    top: 264px;
    margin: 0;
    padding: 0;
    list-style: none;
  }
  .contacts li {
    display: flex;
    align-items: center;
    height: 32px;
    font-size: 26px;
    letter-spacing: 0.3px;
  }
  .contacts svg { width: 22px; height: 22px; margin-right: 20px; flex: none; }

  .back-field {
    position: absolute;
    inset: 0;
    background: var(--navy-card);
  }
  .card-back .wordmark {
    left: 448px;
    top: 268px;
    font-size: 80px;
    color: var(--white);
  }
  .card-back .site {
    position: absolute;
    left: 0; right: 0;
    top: 400px;
    text-align: center;
    font-size: 29px;
    letter-spacing: 0.5px;
  }
</style>
</head>
<body>
  <section class="card card-front">
    <h1 class="wordmark">pexla</h1>
    <div class="identity">
      <span class="person">Marcus Reid</span>
      <span class="role">Founder, Director</span>
    </div>
    <div class="divider"></div>
    <ul class="contacts">
      <li>
        <svg viewBox="0 0 24 24" aria-hidden="true"><path fill="currentColor" d="M6.6 10.8a15.1 15.1 0 0 0 6.6 6.6l2.2-2.2c.3-.3.7-.4 1-.2 1.1.4 2.3.6 3.6.6.6 0 1 .4 1 1V20c0 .6-.4 1-1 1A17 17 0 0 1 3 4c0-.6.4-1 1-1h3.5c.6 0 1 .4 1 1 0 1.3.2 2.5.6 3.6.1.3 0 .7-.2 1z"/></svg>
        +61 (0)412 555 018
      </li>
      <li>
        <svg viewBox="0 0 24 24" aria-hidden="true"><path fill="currentColor" d="M2 5h20v14H2z"/><path fill="none" stroke="#fff" stroke-width="2" d="M3 6l9 7 9-7"/></svg>
        marcus@pexlamedia.com.au
      </li>
      <li>
        <svg viewBox="0 0 24 24" aria-hidden="true" fill="none" stroke="currentColor" stroke-width="1.8"><circle cx="12" cy="12" r="9.5"/><ellipse cx="12" cy="12" rx="4" ry="9.5"/><path d="M2.5 12h19M4 7h16M4 17h16"/></svg>
        www.pexlamedia.com.au
      </li>
    </ul>
  </section>

  <section class="card card-back">
    <div class="back-field" role="img" aria-label="Repeating brand name pattern in tonal navy"></div>
    <h2 class="wordmark">pexla</h2>
    <div class="site">www.pexlamedia.com.au</div>
  </section>
</body>
</html>
```